Wellpath Ledgers New Website

Please review the attached Design Brief with additional details. Thank you!

The goal is to create a website that effectively communicates the benefits of WellPath Ledgers to eye care professionals. The website should streamline the process of understanding and utilizing WellPath Ledgers' services, emphasizing improved patient outcomes, increased referrals, and enhanced patient engagement.

Target Market(s)

Eyecare Professionals

Number of Pages Required

4 page

```html
<!DOCTYPE html>
<html lang="en">
<head>
<meta charset="utf-8">
<title>Wellpath Ledgers</title>
<link href="https://fonts.googleapis.com/css2?family=Open+Sans:wght@400;500;600;700&family=Montserrat:wght@400;500;600&display=swap" rel="stylesheet">
<style>
:root{
  --navy:#1b2a55;
  --navy-deep:#131f42;
  --orange:#f7a631;
  --ink:#1c2233;
  --muted:#7a7f8c;
  --line:#d9dce3;
  --soft:#f3f4f8;
  --blue:#2b6fd1;
  --white:#fff;
}
*{box-sizing:border-box;margin:0;padding:0}
html,body{width:1200px;height:4729px;overflow:hidden}
body{font-family:"Montserrat",sans-serif;color:var(--ink);background:var(--white);position:relative}
.abs{position:absolute}
.head-font{font-family:"Open Sans",sans-serif}
.photo{position:absolute}
.label{position:absolute;font-size:12px;color:var(--orange);letter-spacing:.5px;text-transform:uppercase}
.label.center{left:0;width:100%;text-align:center}
.label.center span{border-bottom:1px solid var(--orange);padding-bottom:4px}
.title{position:absolute;font-family:"Open Sans",sans-serif;font-weight:600;font-size:40px;left:0;width:100%;text-align:center}
.site-header{position:absolute;top:0;left:0;width:1200px;height:103px;background:#f7f7f9}
.brand{position:absolute;display:flex;align-items:center;gap:10px;font-family:"Open Sans",sans-serif;font-weight:600;color:var(--navy)}
.brand i{display:block;border-radius:50%;background:var(--orange)}
.topbar{position:absolute;left:385px;top:0;width:815px;height:34px;background:var(--navy);color:#fff;font-size:11px;font-weight:600}
.topbar div{position:absolute;top:0;height:34px;line-height:34px}
.topbar .appt{left:205px;width:210px;background:var(--orange);text-align:center}
.nav{position:absolute;top:62px;font-size:11px;font-weight:500;color:#333}
.btn-outline{position:absolute;border:1.5px solid var(--blue);color:var(--navy);font-size:10px;font-weight:600;text-align:center}
.hero{position:absolute;top:103px;left:0;width:1200px;height:616px;background:linear-gradient(120deg,#3d4a5c,#1c2431 55%,#2a3340)}
.hero .tag{position:absolute;left:517px;top:196px;width:163px;height:37px;background:var(--orange);color:#fff;font-size:11px;font-weight:600;line-height:37px;text-align:center}
.hero h1{position:absolute;top:245px;left:0;width:100%;text-align:center;font-family:"Open Sans",sans-serif;color:#fff;font-weight:700;font-size:58px;line-height:70px;letter-spacing:.5px}
.hero .ghost{position:absolute;left:515px;top:415px;width:167px;height:45px;border:1px solid #fff;color:#fff;font-size:11px;font-weight:600;line-height:43px;text-align:center}
.about h2{position:absolute;left:621px;top:840px;font-family:"Open Sans",sans-serif;font-weight:600;font-size:40px;line-height:52px}
.about h3{position:absolute;left:621px;top:974px;font-family:"Open Sans",sans-serif;font-weight:500;font-size:20px}
.about p{position:absolute;left:621px;width:500px;font-size:12.5px;line-height:21px;color:var(--muted)}
.btn-solid{position:absolute;background:var(--orange);color:#fff;font-weight:600;text-align:center}
.services{position:absolute;top:1321px;left:0;width:1200px;height:652px;background:var(--soft)}
.svc-icon{position:absolute;width:90px;height:90px;border-radius:50%;background:var(--navy);border:6px solid var(--soft);box-shadow:0 -4px 0 0 var(--orange)}
.svc-icon svg{position:absolute;left:19px;top:19px}
.svc-name{position:absolute;width:274px;height:95px;background:#fff;box-shadow:0 6px 18px rgba(0,0,0,.08);font-family:"Open Sans",sans-serif;font-weight:500;font-size:19px;line-height:95px;text-align:center}
.callband{position:absolute;top:1973px;left:0;width:1200px;height:257px;background:linear-gradient(180deg,#1b2a55,#22325f)}
.callband h2{position:absolute;top:90px;left:0;width:100%;text-align:center;font-family:"Open Sans",sans-serif;font-weight:500;color:#fff;font-size:32px;line-height:39px}
.callband h2 em{font-style:normal;color:var(--orange)}
.callbox{position:absolute;left:351px;top:2199px;width:500px;height:59px;background:#fff;box-shadow:0 4px 14px rgba(0,0,0,.12);font-family:"Open Sans",sans-serif;font-size:15px;display:flex;align-items:center;justify-content:space-around;padding:0 18px}
.why-card{position:absolute;width:233px;height:262px;background:#fff;box-shadow:0 4px 16px rgba(0,0,0,.08);text-align:center}
.why-card .ic{position:absolute;left:76px;top:30px;width:80px;height:80px;border-radius:50%;background:#eef0f4}
.why-card .ic svg{position:absolute;left:24px;top:24px}
.why-card h4{position:absolute;top:145px;left:0;width:100%;font-family:"Open Sans",sans-serif;font-weight:500;font-size:18px}
.why-card p{position:absolute;top:175px;left:20px;width:193px;font-size:12.5px;line-height:23px;color:#555}
.why-card.active{background:var(--orange)}
.why-card.active h4,.why-card.active p{color:#fff}
.why-card.active .ic{background:#fff}
.reviews-band{position:absolute;top:3068px;left:0;width:1200px;height:360px;background:linear-gradient(180deg,#26355f,#1b2a55)}
.review{position:absolute;top:3310px;width:299px;height:327px;background:#fff;box-shadow:0 6px 20px rgba(0,0,0,.08)}
.review .q{position:absolute;left:-26px;top:40px;width:46px;height:46px;border-radius:50%;background:var(--orange)}
.review .q svg{position:absolute;left:11px;top:13px}
.review .stars{position:absolute;left:40px;top:40px;color:#e5473a;font-size:17px;letter-spacing:3px}
.review p{position:absolute;left:40px;top:78px;width:220px;font-size:12.5px;line-height:24px;color:#777}
.review hr{position:absolute;left:40px;top:200px;width:220px;border:0;border-top:1px solid #bbb}
.review .av{position:absolute;left:40px;top:232px;width:54px;height:54px;border-radius:50%;background:#c9ccd4}
.review .who{position:absolute;left:110px;top:235px;font-size:14px;font-weight:600;color:#333}
.review .role{position:absolute;left:110px;top:260px;font-size:12.5px;color:#888}
.footer-band{position:absolute;top:4190px;left:0;width:1200px;height:539px;background:var(--navy)}
.contact-card{position:absolute;left:138px;top:3868px;width:921px;height:457px;background:#fff;box-shadow:0 8px 28px rgba(0,0,0,.1);border-radius:14px;overflow:hidden}
.field{position:absolute;border:1px solid var(--line);font-size:11px;color:#777;padding:10px 8px}
.foot-nav{position:absolute;top:4487px;font-family:"Open Sans",sans-serif;font-size:14px;color:#fff}
.foot-item{position:absolute;top:4572px;color:#fff;font-size:12px;line-height:18px}
.foot-item .ring{position:absolute;left:0;top:-8px;width:56px;height:56px;border-radius:50%;border:1.5px solid rgba(255,255,255,.6)}
.foot-item .ring svg{position:absolute;left:15px;top:15px}
.bottom-bar{position:absolute;top:4667px;left:0;width:1200px;height:62px;background:var(--orange)}
.social{position:absolute;top:20px;width:22px;height:22px;border:1px solid #fff}
</style>
</head>
<body>

<header class="site-header">
  <div class="brand" style="left:125px;top:24px;font-size:26px">
    <i style="width:26px;height:26px"></i><span>Wellpath Ledgers</span>
  </div>
  <div class="topbar">
    <div style="left:60px">&#9742; 555 - 010 - 4821</div>
    <div class="appt">REQUEST AN APPOINTMENT</div>
    <div style="left:475px">&#9679; 48 Harbor Lane East</div>
  </div>
  <nav>
    <span class="nav" style="left:397px">Home</span>
    <span class="nav" style="left:472px">About Us</span>
    <span class="nav" style="left:545px">Services</span>
    <span class="nav" style="left:622px">Our Team</span>
    <span class="nav" style="left:709px">Blog</span>
  </nav>
  <div class="btn-outline" style="left:932px;top:55px;width:118px;height:32px;line-height:29px">CONTACT US</div>
</header>

<section class="hero" role="img" aria-label="Photo of a medical worker reviewing an invoice at a desk with a computer">
  <div class="tag">WELCOME</div>
  <h1>Champions of<br>Medical Registries Services</h1>
  <div class="ghost">ABOUT COMPANY</div>
</section>

<section class="about">
  <div class="photo" style="left:90px;top:857px;width:247px;height:365px;background:linear-gradient(160deg,#c9d6e3,#7c97b4)" role="img" aria-label="Photo of a doctor with a stethoscope"></div>
  <div class="photo" style="left:350px;top:811px;width:228px;height:222px;background:linear-gradient(160deg,#e9ecef,#9aa6b4)" role="img" aria-label="Photo of a doctor in a white coat holding a tablet"></div>
  <div class="photo" style="left:350px;top:1046px;width:228px;height:222px;background:linear-gradient(160deg,#5d6d80,#2d3a4a)" role="img" aria-label="Photo of colleagues meeting around a laptop"></div>
  <div class="abs" style="left:297px;top:997px;width:100px;height:100px;border-radius:50%;background:#fff;box-shadow:0 4px 14px rgba(0,0,0,.12)"></div>
  <div class="label" style="left:621px;top:808px">Who we are</div>
  <h2>Revolutionizing Eye<br>Health Management</h2>
  <h3>Caring for Eyes, Connecting with Data</h3>
  <p style="top:1018px">Lorem ipsum dolor sit amet, consectetur adipiscing elit, sed do eiusmod temp or incididunt ut labore et dolore magna aliqua. Ut enim ad minim veniam, quis labors nisi ut aliquip ex ea commodo consequat.</p>
  <p style="top:1094px">Lorem ipsum dolor sit amet, consectetur adipiscing elit, sed do eiusmod temp or incididunt ut labore et dolore magna aliqua.</p>
  <div class="btn-solid" style="left:620px;top:1177px;width:153px;height:43px;line-height:43px;font-size:15px">Contact us &nbsp;&rarr;</div>
</section>

<section class="services">
  <div class="label center" style="top:76px"><span>Our services</span></div>
  <div class="title" style="top:112px">Leading Registries Services</div>
</section>
<div class="photo" style="left:90px;top:1595px;width:325px;height:263px;background:linear-gradient(160deg,#c7d2de,#6f8197)" role="img" aria-label="Photo of clinicians reviewing a report"></div>
<div class="photo" style="left:441px;top:1595px;width:325px;height:263px;background:linear-gradient(160deg,#e6dccf,#a8998a)" role="img" aria-label="Photo of a doctor writing notes"></div>
<div class="photo" style="left:792px;top:1595px;width:325px;height:263px;background:linear-gradient(160deg,#c6d4e2,#6a88a8)" role="img" aria-label="Photo of a nurse using a tablet"></div>
<div class="svc-icon" style="left:208px;top:1552px"><svg width="40" height="40" viewBox="0 0 40 40" fill="none" stroke="#fff" stroke-width="2"><path d="M8 20a12 12 0 0 1 20-9M32 20a12 12 0 0 1-20 9"/><path d="M28 5v6h-6M12 35v-6h6"/><path d="M20 13c3 4 5 6 5 9a5 5 0 0 1-10 0c0-3 2-5 5-9z"/></svg></div>
<div class="svc-icon" style="left:559px;top:1552px"><svg width="40" height="40" viewBox="0 0 40 40" fill="none" stroke="#fff" stroke-width="2"><path d="M20 6l12 9-5 15H13L8 15z"/><circle cx="20" cy="6" r="2"/><circle cx="32" cy="15" r="2"/><circle cx="8" cy="15" r="2"/></svg></div>
<div class="svc-icon" style="left:910px;top:1552px"><svg width="40" height="40" viewBox="0 0 40 40" fill="none" stroke="#fff" stroke-width="2"><path d="M8 34h24M14 28h14M20 28l-6-14 6-6 6 8z"/><circle cx="27" cy="10" r="3"/></svg></div>
<div class="svc-name" style="left:116px;top:1812px">Health Analytics</div>
<div class="svc-name" style="left:467px;top:1812px">Outcome Monitoring</div>
<div class="svc-name" style="left:818px;top:1812px">Data Management</div>

<section class="callband">
  <h2>We're On <em>Call 24/7</em> to React Promptly to Your<br>Needs, Don't Hesitate to Call</h2>
</section>

<div class="photo" style="left:780px;top:2230px;width:420px;height:838px;background:linear-gradient(180deg,#e9eef3,#9fb6cf 60%,#6d8cb0)" role="img" aria-label="Photo of a smiling professional woman with crossed arms"></div>
<div class="callbox"><span>+ (001) 555-010-200</span><span>[or]</span><span>hello@wellpath.test</span></div>
<div class="label center" style="top:2310px"><span>Why choose us</span></div>
<div class="title" style="top:2345px">Why Choose Us</div>

<div class="why-card" style="left:97px;top:2470px"><div class="ic"><svg width="32" height="32" viewBox="0 0 32 32" fill="none" stroke="#333" stroke-width="2"><path d="M5 22a11 11 0 1 1 22 0"/><path d="M16 22l-3-8"/></svg></div><h4>Client Focus</h4><p>Everything we do revolves around our clients and their needs</p></div>
<div class="why-card active" style="left:354px;top:2470px"><div class="ic"><svg width="32" height="32" viewBox="0 0 32 32" fill="none" stroke="#f7a631" stroke-width="2"><circle cx="16" cy="16" r="9"/><path d="M16 3v26M3 16h26"/></svg></div><h4>Innovative Solutions</h4><p>Everything we do revolves around our clients and their needs</p></div>
<div class="why-card" style="left:610px;top:2470px"><div class="ic"><svg width="32" height="32" viewBox="0 0 32 32" fill="none" stroke="#333" stroke-width="2"><path d="M6 14a10 10 0 0 1 18-5M26 18a10 10 0 0 1-18 5"/><path d="M24 4v5h-5M8 28v-5h5"/></svg></div><h4>Cost-Effective</h4><p>Everything we do revolves around our clients and their needs</p></div>
<div class="why-card" style="left:97px;top:2754px"><div class="ic"><svg width="32" height="32" viewBox="0 0 32 32" fill="none" stroke="#333" stroke-width="2"><circle cx="16" cy="11" r="6"/><path d="M5 28c0-6 5-9 11-9s11 3 11 9z"/></svg></div><h4>Quality Assurance</h4><p>Everything we do revolves around our clients and their needs</p></div>
<div class="why-card" style="left:354px;top:2754px"><div class="ic"><svg width="32" height="32" viewBox="0 0 32 32" fill="none" stroke="#333" stroke-width="2"><circle cx="14" cy="16" r="11"/><path d="M3 16h22M14 5c4 4 4 18 0 22M14 5c-4 4-4 18 0 22"/><circle cx="24" cy="23" r="4" fill="#eef0f4"/></svg></div><h4>Global Reach</h4><p>Everything we do revolves around our clients and their needs</p></div>
<div class="why-card" style="left:610px;top:2754px"><div class="ic"><svg width="32" height="32" viewBox="0 0 32 32" fill="none" stroke="#333" stroke-width="2"><circle cx="16" cy="10" r="4"/><circle cx="7" cy="13" r="3"/><circle cx="25" cy="13" r="3"/><path d="M9 27c0-5 3-8 7-8s7 3 7 8zM2 25c0-4 2-6 5-6M30 25c0-4-2-6-5-6"/></svg></div><h4>Cost-Effective</h4><p>Everything we do revolves around our clients and their needs</p></div>

<section class="reviews-band" role="img" aria-label="Dimmed photo of a clinic interior">
  <div class="label center" style="top:100px;color:#fff"><span style="border-color:#fff">Testimonials</span></div>
  <div class="title" style="top:132px;color:#fff">Reviews from Clients</div>
</section>
<div class="review" style="left:112px"><div class="q"><svg width="24" height="20" viewBox="0 0 24 20" fill="#fff"><rect x="1" y="2" width="9" height="9"/><path d="M10 11L6 18H3l3-7z"/><rect x="13" y="2" width="9" height="9"/><path d="M22 11l-4 7h-3l3-7z"/></svg></div><div class="stars">&#9733;&#9733;&#9733;&#9733;&#9733;</div><p>Lorem ipsum dolor sit amet, co nsectetur adipiscing elit, sed do eiusmod tempor incididunt ut labore et dolore</p><hr><div class="av" role="img" aria-label="Reviewer portrait"></div><div class="who">Mara Linden</div><div class="role">Human Resource</div></div>
<div class="review" style="left:461px"><div class="q"><svg width="24" height="20" viewBox="0 0 24 20" fill="#fff"><rect x="1" y="2" width="9" height="9"/><path d="M10 11L6 18H3l3-7z"/><rect x="13" y="2" width="9" height="9"/><path d="M22 11l-4 7h-3l3-7z"/></svg></div><div class="stars">&#9733;&#9733;&#9733;&#9733;&#9733;</div><p>Lorem ipsum dolor sit amet, co nsectetur adipiscing elit, sed do eiusmod tempor incididunt ut labore et dolore</p><hr><div class="av" role="img" aria-label="Reviewer portrait"></div><div class="who">Mara Linden</div><div class="role">Human Resource</div></div>
<div class="review" style="left:807px"><div class="q"><svg width="24" height="20" viewBox="0 0 24 20" fill="#fff"><rect x="1" y="2" width="9" height="9"/><path d="M10 11L6 18H3l3-7z"/><rect x="13" y="2" width="9" height="9"/><path d="M22 11l-4 7h-3l3-7z"/></svg></div><div class="stars">&#9733;&#9733;&#9733;&#9733;&#9733;</div><p>Lorem ipsum dolor sit amet, co nsectetur adipiscing elit, sed do eiusmod tempor incididunt ut labore et dolore</p><hr><div class="av" role="img" aria-label="Reviewer portrait"></div><div class="who">Mara Linden</div><div class="role">Human Resource</div></div>

<div class="footer-band"></div>

<div class="label center" style="top:3716px"><span>Contact us</span></div>
<div class="title" style="top:3750px">Get in touch with us</div>
<div class="contact-card">
  <div class="photo" style="left:0;top:0;width:459px;height:457px;background:linear-gradient(150deg,#c8d3df,#4f6c90)" role="img" aria-label="Photo of technicians examining a circuit board at a workstation"></div>
  <div class="brand" style="left:511px;top:50px;font-size:24px"><i style="width:20px;height:20px"></i><span>Wellpath Ledgers</span></div>
  <div class="abs head-font" style="left:511px;top:104px;font-size:27px;color:#333">Please fill out the form</div>
  <div class="field" style="left:511px;top:167px;width:361px;height:38px">Name</div>
  <div class="field" style="left:511px;top:220px;width:174px;height:38px">Phone</div>
  <div class="field" style="left:698px;top:220px;width:174px;height:38px">Email</div>
  <div class="field" style="left:511px;top:272px;width:361px;height:70px">Message</div>
  <div class="btn-solid" style="left:511px;top:360px;width:361px;height:38px;line-height:38px;font-size:11px">Send</div>
</div>

<footer>
  <div class="brand" style="left:0;width:1200px;justify-content:center;top:4385px;font-size:34px;color:#fff"><i style="width:30px;height:30px"></i><span>Wellpath Ledgers</span></div>
  <span class="foot-nav" style="left:352px">HOME</span>
  <span class="foot-nav" style="left:446px">SERVICES</span>
  <span class="foot-nav" style="left:552px">ABOUT US</span>
  <span class="foot-nav" style="left:671px">TESTIMONIALS</span>
  <span class="foot-nav" style="left:821px">BLOG</span>
  <div class="abs" style="left:140px;top:4540px;width:920px;border-top:1px solid rgba(255,255,255,.25)"></div>
  <div class="foot-item" style="left:174px"><div class="ring"><svg width="24" height="24" viewBox="0 0 24 24" fill="none" stroke="#fff" stroke-width="1.5"><circle cx="12" cy="12" r="10"/><path d="M2 12h20M12 2c4 4 4 16 0 20M12 2c-4 4-4 16 0 20"/></svg></div><div style="padding-left:68px;font-size:11px">48 Harbor Lane, Suite 2<br>Riverton, ST 00000</div></div>
  <div class="abs" style="left:430px;top:4557px;height:62px;border-left:1px solid rgba(255,255,255,.3)"></div>
  <div class="foot-item" style="left:505px"><div class="ring"><svg width="24" height="24" viewBox="0 0 24 24" fill="none" stroke="#fff" stroke-width="1.5"><rect x="7" y="2" width="10" height="20" rx="2"/><path d="M11 18h2"/></svg></div><div style="padding-left:68px">PHONE<br><span style="font-size:11px">(555) 010 7788</span></div></div>
  <div class="abs" style="left:753px;top:4557px;height:62px;border-left:1px solid rgba(255,255,255,.3)"></div>
  <div class="foot-item" style="left:829px"><div class="ring"><svg width="24" height="24" viewBox="0 0 24 24" fill="none" stroke="#fff" stroke-width="1.5"><rect x="3" y="6" width="18" height="13"/><path d="M3 6l9 7 9-7"/></svg></div><div style="padding-left:68px">EMAIL<br><span style="font-size:11px">office@wellpath.test</span></div></div>
  <div class="bottom-bar">
    <div class="abs" style="left:148px;top:22px;font-size:11px;color:#fff">Wellpath Ledgers</div>
    <div class="social" style="left:932px"></div>
    <div class="social" style="left:966px"></div>
    <div class="social" style="left:1000px"></div>
    <div class="social" style="left:1034px"></div>
  </div>
</footer>

</body>
</html>
```